The Harbor Promise (Poster Design ) for TV Show

“The Harbor Promise” tells the inspirational stories of the men and women who founded and built incredible companies from nothing. The show is hosted by Laurel-nominated actor Dale Whitcombe.

Looking for a inspirational poster design for a TV show

Design i like
https://img.craftloom.example/48210377/r/il/b4e1d2/2947106615/il_1588xN.2947106615_qk7m.jpg

https://media.pitchvault.example/Rt518LkWzN4HD9mP2aE7yQbXvcA=/375x231:1749x1605/500x500/top/smart/pitchvault-attachments/208/208471/attachment_208471593

https://thumbs.seekmore.example/images?q=tbn:XbR4tw9Lmz2Kq8Vn3PaHcUeYd7_JF6gsBpWRt&usqp=CAU

https://files.pagecraft.example/content/v1/6a3c91f2b8475dd1e3ab9264/2847361950218-KTW8M3QNZPLH42F9XAD5/QWTRMPK.jpg

https://static.reelhaven.example/images/journal/post_images/47205/images-w1400.jpg?1739204681

https://img.chatterbox.example/7k2wpd9xhn384.jpg

https://i.moodpin.example/736x/3c/8d/b1/3c8db1f72a0954e1d6c83b905f24e17c--film-posters-poster-design.jpg

Segment of the show to get a better understanding
https://clipstream.example/582049163/b7e3c915a2

Font styles to use
Serif
Sans Serif
Script

Requirements
Must have
• The Harbor Promise

```html
<!DOCTYPE html>
<html lang="en">
<head>
<meta charset="utf-8">
<title>The Harbor Promise — TV Show Poster</title>
<link rel="stylesheet" href="https://fonts.googleapis.com/css2?family=Montserrat:wght@400;500;700;800&display=swap">
<style>
  :root {
    --backdrop: #f2f2f2;
    --poster-black: #101010;
    --ink-white: #ffffff;
    --gold-light: #fde98a;
    --gold-mid: #e0b23a;
    --gold-deep: #b57a0a;
    --pedestal: #1c1c1c;
  }
  html, body {
    margin: 0;
    padding: 0;
    width: 1200px;
    height: 1200px;
    overflow: hidden;
    background: var(--backdrop);
  }
  .poster {
    position: absolute;
    left: 212px;
    top: 37px;
    width: 783px;
    height: 1105px;
    background: var(--poster-black);
    font-family: "Montserrat", sans-serif;
    color: var(--ink-white);
    box-shadow: 0 4px 14px rgba(0,0,0,0.18);
  }
  .title-rule {
    position: absolute;
    left: 200px;
    top: 51px;
    width: 1.5px;
    height: 513px;
    background: var(--ink-white);
  }
  .title-the {
    position: absolute;
    left: 54px;
    top: 72px;
    margin: 0;
    font-size: 60px;
    font-weight: 800;
    line-height: 1;
    letter-spacing: -1px;
  }
  .title-main {
    position: absolute;
    right: 51px;
    font-size: 98px;
    font-weight: 700;
    line-height: 1;
    letter-spacing: -1px;
    text-align: right;
    white-space: nowrap;
  }
  .title-harbor { top: 131px; }
  .title-promise {
    top: 226px;
    background: linear-gradient(90deg, var(--gold-light) 0%, var(--gold-mid) 25%, var(--gold-deep) 50%, var(--gold-mid) 78%, var(--gold-light) 100%);
    -webkit-background-clip: text;
    background-clip: text;
    color: transparent;
  }
  .tagline {
    position: absolute;
    right: 51px;
    top: 324px;
    margin: 0;
    font-size: 22px;
    font-weight: 500;
    line-height: 31px;
    text-align: right;
    white-space: nowrap;
  }
  .host-credit {
    position: absolute;
    right: 51px;
    top: 917px;
    display: flex;
    align-items: flex-end;
    gap: 14px;
  }
  .statuette {
    width: 48px;
    height: 131px;
    display: block;
  }
  .host-text {
    text-align: right;
    padding-right: 8px;
    border-right: 1.5px solid var(--ink-white);
    margin-bottom: -8px;
    padding-top: 4px;
    padding-bottom: 6px;
  }
  .host-intro {
    font-size: 14px;
    font-weight: 500;
    line-height: 1.3;
    margin-bottom: 4px;
  }
  .host-accolade,
  .host-name {
    font-size: 33px;
    font-weight: 700;
    line-height: 36px;
    white-space: nowrap;
    letter-spacing: -0.5px;
  }
  .host-accolade {
    background: linear-gradient(90deg, var(--gold-light) 0%, var(--gold-mid) 35%, var(--gold-deep) 65%, var(--gold-mid) 100%);
    -webkit-background-clip: text;
    background-clip: text;
    color: transparent;
  }
</style>
</head>
<body>
  <main class="poster">
    <div class="title-rule"></div>
    <h1 class="title-the">THE</h1>
    <div class="title-main title-harbor">HARBOR</div>
    <div class="title-main title-promise">PROMISE</div>
    <p class="tagline">tells the inspirational stories of the men and<br>women who founded and built incredible<br>companies from nothing.</p>

    <div class="host-credit">
      <svg class="statuette" viewBox="0 0 48 131" role="img" aria-label="Golden award statuette on a black pedestal">
        <defs>
          <linearGradient id="statuetteGold" x1="0" x2="1" y1="0" y2="0">
            <stop offset="0" stop-color="#8a5a06"/>
            <stop offset="0.5" stop-color="#f1cf6a"/>
            <stop offset="1" stop-color="#8a5a06"/>
          </linearGradient>
        </defs>
        <rect x="14" y="0" width="20" height="104" rx="8" fill="url(#statuetteGold)"/>
        <rect x="4" y="104" width="40" height="27" rx="3" fill="var(--pedestal)"/>
      </svg>
      <div class="host-text">
        <div class="host-intro">THE SHOW IS HOSTED BY</div>
        <div class="host-accolade">LAUREL-NOMINATED</div>
        <div class="host-name">ACTOR DALE WHITCOMBE</div>
      </div>
    </div>
  </main>
</body>
</html>
```